Website for new dental office

I am Dr. Colin Ashford and am building a new dental practice. I specialize in general dentistry. I am young and have a higher end dental practice incorporating very new technologies and would like my website to reflect that. As many dental patients are older, the website must be very easy to navigate. I would like patients to be able to request appointments, and will eventually add on patient information forms (the health history, etc, that you normally fill out in the practice) from my practice management software, so leave an area for that.

Industry/Entity Type

Building

```html
<!DOCTYPE html>
<html lang="en">
<head>
<meta charset="utf-8">
<title>Ashford Dental Clinic</title>
<link rel="stylesheet" href="https://fonts.googleapis.com/css2?family=Source+Sans+3:ital,wght@0,400;0,600;1,600&display=swap">
<style>
:root{
  --teal:#19b7c9;
  --teal-dark:#0aa5b8;
  --ink:#333333;
  --body:#555555;
  --rule:#cfcfcf;
  --field:#ececec;
  --btn:#2b2b2b;
  --white:#ffffff;
}
*{box-sizing:border-box;margin:0;padding:0}
html,body{width:928px;height:1200px;overflow:hidden;background:var(--white);font-family:"Source Sans 3",Arial,sans-serif;color:var(--body)}
.page{position:relative;width:928px;height:1200px}
.abs{position:absolute}
.site-header{left:0;top:0;width:928px;height:82px;background:var(--teal)}
.brand{left:160px;top:22px;display:flex;align-items:center;gap:8px;color:var(--white);font-size:22px;font-weight:600}
.brand-dot{width:22px;height:22px;border-radius:50%;background:var(--white)}
.phone{left:650px;top:29px;display:flex;align-items:center;gap:8px;color:var(--white);font-size:13px}
.main-nav{left:0;top:82px;width:928px;height:40px;background:var(--teal-dark);display:flex;align-items:center;padding-left:154px}
.main-nav a{color:var(--white);text-decoration:none;font-size:10px;padding:0 22px;height:22px;line-height:22px;border-right:1px solid rgba(255,255,255,.35)}
.main-nav a:last-child{border-right:none}
.main-nav a:first-child{padding-left:18px}
.hero{left:154px;top:140px;width:620px;height:242px;background:linear-gradient(90deg,#d9d3cf 0%,#e8c8b8 35%,#9fb9d7 65%,#3f7fc4 100%)}
.hero-tagline{right:19px;top:40px;text-align:right;color:var(--white);font-style:italic;font-weight:600;font-size:13px;line-height:22px}
.hero-dots{right:9px;bottom:7px;display:flex;gap:3px}
.hero-dots span{width:5px;height:5px;background:#666}
.hero-dots span:first-child{background:var(--teal)}
.section-title{font-size:15px;color:var(--ink);font-weight:400}
.rule{height:1px;background:var(--rule)}
.photo{background:#ddd}
.copy{font-size:7px;line-height:12.4px;text-align:justify;color:var(--body)}
.btn-more{display:inline-block;background:var(--btn);color:var(--white);font-size:7.5px;border-radius:3px;padding:0 7px;height:19px;line-height:19px}
.field{left:154px;width:174px;background:var(--field);font-size:7px;color:#666;padding:9px 10px}
.submit{left:154px;top:1038px;width:143px;height:28px;background:var(--btn);color:var(--white);font-size:12px;font-weight:600;letter-spacing:.5px;display:flex;align-items:center;justify-content:center;gap:10px}
.news-item{left:412px;width:362px}
.news-thumb{position:absolute;left:0;top:0;width:55px;height:49px}
.news-body{position:absolute;left:70px;top:0;width:292px;font-size:7.5px;line-height:13.5px}
.news-author{color:var(--teal)}
.news-date{color:var(--ink)}
.site-footer{left:0;top:1120px;width:928px;height:80px;background:var(--teal)}
.footer-nav{left:156px;top:1146px;font-size:7px;color:var(--white)}
.footer-copy{left:153px;top:1165px;font-size:6.5px;color:var(--white)}
.social{left:668px;top:1149px;display:flex;gap:7px}
.social span{width:20px;height:20px;border-radius:50%;background:#2f8fc9;border:2px solid var(--white)}
</style>
</head>
<body>
<div class="page">
  <header class="abs site-header"></header>
  <div class="abs brand"><span class="brand-dot"></span>Ashford Dental Clinic</div>
  <div class="abs phone">
    <svg width="22" height="14" viewBox="0 0 22 14"><path d="M1 5c0-3 20-3 20 0l-1 2h-4l-1-2H7L6 7H2z" fill="#fff"/><rect x="5" y="7" width="12" height="7" rx="1.5" fill="#fff"/><g fill="#19b7c9"><rect x="8" y="9" width="1.5" height="1.5"/><rect x="10.3" y="9" width="1.5" height="1.5"/><rect x="12.6" y="9" width="1.5" height="1.5"/><rect x="8" y="11.3" width="1.5" height="1.5"/><rect x="10.3" y="11.3" width="1.5" height="1.5"/><rect x="12.6" y="11.3" width="1.5" height="1.5"/></g></svg>
    0198 765 4320
  </div>
  <nav class="abs main-nav">
    <a>Home</a><a>About</a><a>Services</a><a>Solutions</a><a>Blog</a><a>Testimonials</a><a>Conatact</a>
  </nav>

  <section class="abs hero" role="img" aria-label="Photo of a dentist treating a smiling patient in the chair">
    <p class="abs hero-tagline">Higher End Dental Practice<br>Incorporating Very New Technologies</p>
    <div class="abs hero-dots"><span></span><span></span><span></span><span></span></div>
  </section>

  <h2 class="abs section-title" style="left:154px;top:404px">Welcome to Ashford Dental Clinic</h2>
  <div class="abs rule" style="left:154px;top:432px;width:620px"></div>
  <div class="abs photo" style="left:154px;top:452px;width:131px;height:126px;background:linear-gradient(135deg,#f1e3dc,#e6c4b3)" role="img" aria-label="Photo of a mother and daughter brushing their teeth"></div>
  <p class="abs copy" style="left:300px;top:452px;width:474px">Nemo enim ipsam voluptatem quia voluptas sit aspernatur aut odit aut fugit sed quia consequuntur magni dolores eos voluptatem ondimentum aenean ut eget wisi ut molestie mauris . Nemo enim ipsam voluptatem quia oluptas sit aspernatur aut odit aut fugit sed quia consequuntur magni dolores eos voluptatem ondimentum aenean ut eget wisi ut molestie mauris . Nemo enim ipsam voluptatem quia oluptas sit aspernatur aut odit aut fugit sed quia consequuntur magni dolores eos voluptatem ondimentum aenean ut eget wisi ut molestie mauris . Nemo enim ipsam voluptatem quia oluptas sit aspernatur aut odit aut fugit sed quia consequuntur magni dolores eos voluptatem ondimentum aenean ut eget wisi ut molestie mauris . Nemo enim ipsam voluptatem quia oluptas sit aspernatur aut odit aut fugit sed quia consequuntur magni dolores eos voluptatem ondimentum aenean ut eget wisi ut molestie mauris . Nemo enim ipsam voluptatem quia oluptas sit aspernatur aut odit aut fugit sed quia consequuntur magni dolores eos voluptatem ondimentum aenean ut eget wisi ut molestie mauris .</p>
  <span class="abs btn-more" style="left:303px;top:560px">MORE INFO</span>

  <h2 class="abs section-title" style="left:157px;top:614px">We are Working for your Prefect Smile</h2>
  <div class="abs rule" style="left:154px;top:650px;width:620px"></div>

  <div class="abs photo" style="left:154px;top:678px;width:101px;height:65px;background:linear-gradient(135deg,#e9cdbf,#5c8fc2)" role="img" aria-label="Photo of a dentist examining a patient"></div>
  <p class="abs copy" style="left:266px;top:680px;width:178px;line-height:13.6px">Sed ut perspiciatis, unde omnis iste natus error sit voluptatem accusantium doloremque laudantium totam rem aperiam eaque ipsa quae ab illo inventore veritatis et quasi architecto beatae vitae dicta sunt, explicabo. Nemo enim ipsam voluptatem, quia voluptas.</p>
  <span class="abs btn-more" style="left:155px;top:755px">MORE INFO</span>

  <div class="abs photo" style="left:482px;top:678px;width:101px;height:65px;background:linear-gradient(135deg,#f3e2d6,#e0b59c)" role="img" aria-label="Photo of a bright smile with white teeth"></div>
  <p class="abs copy" style="left:594px;top:680px;width:180px;line-height:13.6px">Sed ut perspiciatis, unde omnis iste natus error sit voluptatem accusantium doloremque laudantium totam rem aperiam eaque ipsa quae ab illo inventore veritatis et quasi architecto beatae vitae dicta sunt, explicabo. Nemo enim ipsam voluptatem, quia voluptas.</p>
  <span class="abs btn-more" style="left:483px;top:755px">MORE INFO</span>

  <h2 class="abs section-title" style="left:154px;top:819px">Request Appointment</h2>
  <div class="abs field" style="top:858px;height:21px;padding-top:6px">Name</div>
  <div class="abs field" style="top:894px;height:22px;padding-top:7px">E Mail</div>
  <div class="abs field" style="top:932px;height:22px;padding-top:6px">Phone</div>
  <div class="abs field" style="top:968px;height:55px;padding-top:7px">Message</div>
  <div class="abs submit">
    <svg width="12" height="12" viewBox="0 0 12 12"><circle cx="6" cy="6" r="6" fill="#444"/><path d="M4.5 3.5l4 2.5-4 2.5z" fill="#fff"/></svg>
    SUBMIT
  </div>
  <div class="abs" style="left:377px;top:821px;width:1px;height:249px;background:var(--rule)"></div>

  <h2 class="abs section-title" style="left:412px;top:816px">Latest News</h2>
  <article class="abs news-item" style="top:853px">
    <div class="news-thumb" style="background:linear-gradient(135deg,#d9a89a,#7b4a40)" role="img" aria-label="Photo of a dental check-up"></div>
    <div class="news-body" style="top:-2px"><div class="news-author">@John Doe</div>Voluptatem quia voluptas sit aspernatur aut odit aut fugit sed quia consequuntur magni dolores eos qui ratione voluptatem sequi.<div class="news-date">[ 21-04-2014 ]</div></div>
  </article>
  <div class="abs rule" style="left:482px;top:917px;width:292px;background:#999"></div>
  <article class="abs news-item" style="top:934px">
    <div class="news-thumb" style="background:linear-gradient(90deg,#e5a894,#f4e6e0,#e5a894)" role="img" aria-label="Photo of teeth with braces"></div>
    <div class="news-body" style="top:-2px"><div class="news-author">@John Doe</div>Duis aute irure dolor in reprehenderit quaerat voluptatem. Ut enim ad minima veniam, quis nostrum exercitationem ullam corporis susc.<div class="news-date">[ 18-04-2014 ]</div></div>
  </article>
  <div class="abs rule" style="left:482px;top:998px;width:292px;background:#999"></div>
  <article class="abs news-item" style="top:1019px">
    <div class="news-thumb" style="background:linear-gradient(135deg,#5fa9c9,#e8eef2)" role="img" aria-label="Photo of dental instruments at work"></div>
    <div class="news-body" style="top:-2px"><div class="news-author">@John Doe</div>Voluptates repudiandae sint et molestiae laboris nisi ut aliquip ex ea commodo consequat. Duis aute irure dolor in reprehenderit in.<div class="news-date">[ 14-04-2014 ]</div></div>
  </article>

  <footer class="abs site-footer"></footer>
  <div class="abs footer-nav">Home &nbsp;|&nbsp; About &nbsp;|&nbsp; Services &nbsp;|&nbsp; Solutions &nbsp;|&nbsp; Blog &nbsp;|&nbsp; Testimonials &nbsp;|&nbsp; Conatact</div>
  <div class="abs footer-copy">© Copy Right 2014 Ashford Dental Clinic &nbsp;| All Rights Reserved</div>
  <div class="abs social">
    <span></span><span></span><span></span>
    <svg width="20" height="20" viewBox="0 0 20 20"><circle cx="10" cy="10" r="9" fill="#ea5a2e" stroke="#fff" stroke-width="2"/><rect x="5.5" y="7" width="9" height="6.5" fill="#fff"/><path d="M5.5 7l4.5 3.5L14.5 7" fill="none" stroke="#ea5a2e" stroke-width=".9"/></svg>
  </div>
</div>
</body>
</html>
```